Business card for event manager / organizer "waiter service"

Draft of a new valuable business card for my company.
Events, personnel service providers, festivals

```html
<!DOCTYPE html>
<html lang="de">
<head>
<meta charset="utf-8">
<title>Niko's Kellnerservice – Visitenkarte</title>
<link rel="stylesheet" href="https://fonts.googleapis.com/css2?family=Roboto+Slab:wght@400;700&family=Quicksand:wght@300&display=swap">
<style>
  :root {
    --stage: #e9e6e3;
    --ink: #111111;
    --orange: #ec7a1c;
    --card-dark: #26232a;
    --text-light: #f4f4f4;
    --photo-light: #f2f2f2;
    --photo-mid: #b9b9b9;
    --photo-dark: #4a4a4a;
  }
  * { box-sizing: border-box; margin: 0; padding: 0; }
  html, body { width: 1200px; height: 801px; overflow: hidden; }
  body {
    background: var(--stage);
    display: flex; align-items: center; justify-content: center; gap: 40px;
    font-family: "Roboto Slab", serif;
  }
  .card {
    position: relative; width: 540px; height: 350px;
    border-radius: 18px; overflow: hidden;
    box-shadow: 0 6px 18px rgba(0,0,0,.18);
  }

  /* front */
  .card--front { background: var(--photo-light); }
  .concert-photo {
    position: absolute; inset: 0;
    background:
      radial-gradient(ellipse at 55% 20%, #ffffff 0%, var(--photo-light) 35%, transparent 60%),
      linear-gradient(180deg, var(--photo-mid) 0%, var(--photo-light) 45%, var(--photo-mid) 75%, var(--photo-dark) 100%);
  }
  .brand {
    position: absolute; left: 70px; top: 120px;
    display: flex; align-items: center; gap: 16px;
  }
  .brand__mark { width: 64px; height: 64px; background: var(--orange); }
  .brand__name {
    font-weight: 700; font-size: 30px; line-height: 1.05;
    color: var(--ink); text-transform: uppercase; letter-spacing: .5px;
  }
  .tagline {
    position: absolute; left: 150px; top: 210px;
    font-family: "Quicksand", sans-serif; font-weight: 300;
    font-size: 17px; color: var(--ink);
  }

  /* back */
  .card--back { background: var(--card-dark); color: var(--text-light); }
  .monogram-area {
    position: absolute; left: 40px; top: 60px; width: 230px; height: 230px;
    background: radial-gradient(circle at 40% 45%, rgba(255,255,255,.06), transparent 70%);
  }
  .portrait {
    position: absolute; right: 40px; top: 26px;
    width: 96px; height: 96px; border-radius: 50%;
    border: 2px solid var(--orange);
    background: radial-gradient(circle at 50% 40%, #8a8a8a, #3a3a3a 75%);
  }
  .contact {
    position: absolute; right: 34px; top: 140px; text-align: right;
  }
  .contact__name { font-size: 22px; font-weight: 400; text-transform: uppercase; letter-spacing: .5px; }
  .contact__role { font-size: 14px; color: var(--orange); margin-bottom: 10px; }
  .contact__list { list-style: none; font-size: 12.5px; line-height: 20px; }
  .contact__list li { display: flex; justify-content: flex-end; align-items: center; gap: 10px; }
  .contact__list svg { width: 12px; height: 12px; flex: none; fill: var(--orange); }
</style>
</head>
<body>

<section class="card card--front">
  <div class="concert-photo" role="img" aria-label="Schwarz-weißes Konzertfoto mit Bühnenscheinwerfern und jubelndem Publikum"></div>
  <div class="brand">
    <div class="brand__mark"></div>
    <div class="brand__name">Niko's<br>Kellnerservice</div>
  </div>
  <p class="tagline">…denn die nächste Feier kommt bestimmt!</p>
</section>

<section class="card card--back">
  <div class="monogram-area"></div>
  <div class="portrait" role="img" aria-label="Porträtfoto des Inhabers"></div>
  <div class="contact">
    <h1 class="contact__name">Niko Brandauer</h1>
    <p class="contact__role">Inhaber</p>
    <ul class="contact__list">
      <li>02361 555 01 27
        <svg viewBox="0 0 24 24"><path d="M6.6 10.8a15 15 0 0 0 6.6 6.6l2.2-2.2c.3-.3.7-.4 1-.2 1.1.4 2.3.6 3.6.6.6 0 1 .4 1 1V20c0 .6-.4 1-1 1A17 17 0 0 1 3 4c0-.6.4-1 1-1h3.5c.6 0 1 .4 1 1 0 1.3.2 2.5.6 3.6.1.3 0 .7-.2 1z"/></svg></li>
      <li>0170 555 48 12
        <svg viewBox="0 0 24 24"><path d="M7 1h10a2 2 0 0 1 2 2v18a2 2 0 0 1-2 2H7a2 2 0 0 1-2-2V3a2 2 0 0 1 2-2zm0 3v14h10V4zm5 15.5a1 1 0 1 0 0 2 1 1 0 0 0 0-2z"/></svg></li>
      <li>info@nikos-kellnerservice.de
        <svg viewBox="0 0 24 24"><path d="M2 21 23 12 2 3v7l15 2-15 2z"/></svg></li>
      <li>nikos-kellnerservice.de
        <svg viewBox="0 0 24 24"><path d="M12 2a10 10 0 1 0 0 20 10 10 0 0 0 0-20zm0 2c.9 0 2.2 2 2.7 5H9.3C9.8 6 11.1 4 12 4zM4.3 11h3a15 15 0 0 0 0 2h-3a8 8 0 0 1 0-2zm5 0h5.4a13 13 0 0 1 0 2H9.3a13 13 0 0 1 0-2zm7.4 0h3a8 8 0 0 1 0 2h-3a15 15 0 0 0 0-2zM9.3 15h5.4c-.5 3-1.8 5-2.7 5s-2.2-2-2.7-5z"/></svg></li>
      <li>Birkenweg 14, 45700 Musterstadt
        <svg viewBox="0 0 24 24"><path d="M12 2a7 7 0 0 0-7 7c0 5 7 13 7 13s7-8 7-13a7 7 0 0 0-7-7zm0 9.5a2.5 2.5 0 1 1 0-5 2.5 2.5 0 0 1 0 5z"/></svg></li>
      <li>/nikoskellnerservice
        <svg viewBox="0 0 24 24"><circle cx="12" cy="12" r="10"/></svg></li>
    </ul>
  </div>
</section>

</body>
</html>
```